Los Brava Dip – CPG Website with WordPress - Store Locator: WP Maps plugin

Larkfield Food Company is a startup consumer packaged goods (CPG) brand launching its flagship product line — Los Brava Dip. We’re seeking a talented web designer to create a bold, professional, mobile-optimized website using WordPress with a WP Maps store locator to help customers find local retailers.

Our goal is to build a strong online presence that supports both retail growth and direct-to-consumer sales.

See Los Brava _Website_Design_Brief word document.

The website URL is https://losbravadip.example/

Target Market(s)

Consumers of gourmet salsa

Industry/Entity Type

Consumer Packaged Goods - Salsa manufacturer.

Coding

Coded - Design and coding required

Number of Pages Required

5+ page

Requirements
Must have
• The design of the Los Brava Dip website shall emulate the clean, polished aesthetic of Fennigo.example.

```html
<!DOCTYPE html>
<html lang="en">
<head>
<meta charset="utf-8">
<title>Contact Us – Los Brava Dip</title>
<link rel="stylesheet" href="https://fonts.googleapis.com/css2?family=Roboto+Condensed:wght@700&family=Outfit:wght@400;500;700&display=swap">
<style>
:root{
  --red:#c9202a;
  --red-dark:#9e1a1e;
  --ink:#222;
  --grey:#8a8a8a;
  --white:#fff;
  --orange:#e8761a;
}
*{box-sizing:border-box;margin:0;padding:0}
html,body{width:877px;height:1200px;overflow:hidden;background:var(--white)}
body{position:relative;font-family:"Outfit",sans-serif;color:var(--ink)}
.abs{position:absolute}
.site-header{position:absolute;left:0;top:0;width:877px;height:58px;background:var(--white);z-index:3}
.brand-tab{position:absolute;left:73px;top:0;width:119px;height:77px;background:var(--white);border-radius:0 0 60px 60px/0 0 22px 22px;z-index:4;display:flex;align-items:center;justify-content:center}
.brand-name{font-family:"Outfit",sans-serif;font-weight:700;color:var(--red);font-size:20px;letter-spacing:.2px}
.main-nav a{position:absolute;top:23px;font-size:9.6px;font-weight:500;letter-spacing:1.1px;color:var(--ink);text-decoration:none}
.nav-cta{position:absolute;left:689px;top:18px;width:95px;height:25px;border-radius:13px;background:var(--red);color:var(--white);font-size:9.6px;font-weight:500;letter-spacing:1.1px;display:flex;align-items:center;justify-content:center;gap:3px}
.hero{position:absolute;left:0;top:58px;width:877px;height:237px;background:
 radial-gradient(circle at 95% 85%,#5a140c 0 28%,transparent 29%),
 linear-gradient(90deg,#f7ad2a 0%,#f29a22 25%,#e8761a 45%,#d4560f 60%,#9a2411 75%,#6a180c 100%)}
.hero-title{position:absolute;left:0;width:877px;top:142px;text-align:center;font-family:"Roboto Condensed",sans-serif;font-weight:700;font-size:44px;color:var(--white);letter-spacing:.5px}
.eyebrow{position:absolute;left:370px;top:338px;width:97px;height:20px;border-top:1px solid var(--red);border-bottom:1px solid var(--red);color:var(--red);font-size:11px;font-weight:500;letter-spacing:1.4px;text-align:center;line-height:18px}
.section-title{position:absolute;left:0;width:877px;top:360px;text-align:center;font-family:"Roboto Condensed",sans-serif;font-weight:700;font-size:31px;color:var(--ink)}
.email-line{position:absolute;left:0;width:842px;top:412px;text-align:center;font-size:15px}
.contact-form{position:absolute;left:134px;top:466px;width:591px;height:317px;border:1px solid var(--red)}
.field{position:absolute;border:1px solid var(--grey);background:var(--white);font-size:12.5px;color:var(--ink);padding:0 16px;display:flex;align-items:center}
.field.message{align-items:flex-start;padding-top:12px}
.send-btn{position:absolute;left:216px;top:253px;width:163px;height:39px;border-radius:20px;background:var(--red);color:var(--white);font-weight:700;font-size:13px;display:flex;align-items:center;justify-content:center;letter-spacing:-.2px}
.follow-band{position:absolute;left:0;top:853px;width:877px;height:204px;background:
 radial-gradient(circle at 100% 110%,#9e1a1e 0 32%,transparent 33%),
 linear-gradient(90deg,#dc5424 0%,#d8441e 40%,#c42a1e 60%,#b41f1e 100%)}
.follow-title{position:absolute;left:278px;top:40px;width:296px;height:35px;border-top:1px solid rgba(255,255,255,.8);border-bottom:1px solid rgba(255,255,255,.8);color:var(--white);font-weight:700;font-size:20px;text-align:center;line-height:33px;letter-spacing:.3px}
.social-ring{position:absolute;top:103px;width:58px;height:58px;border:2px solid var(--white);border-radius:50%}
.social-dot{position:absolute;left:14px;top:14px;width:26px;height:26px;border-radius:50%;background:var(--white)}
.site-footer{position:absolute;left:0;top:1057px;width:877px;height:143px}
.footer-divider-v{position:absolute;left:223px;top:0;width:1px;height:143px;background:#ddd}
.footer-divider-h{position:absolute;left:223px;top:84px;width:649px;height:1px;background:#ddd}
.footer-brand{position:absolute;left:40px;top:52px;width:168px;text-align:center;font-weight:700;color:var(--red);font-size:25px}
.footer-nav span{position:absolute;top:46px;font-size:10px;letter-spacing:1.1px;font-weight:500}
.footer-nav i{position:absolute;top:51px;width:3px;height:3px;background:var(--red)}
.legal{position:absolute;top:104px;font-size:9px;color:var(--ink)}
.mini-social{position:absolute;top:102px;width:20px;height:20px;border-radius:50%;background:var(--ink)}
</style>
</head>
<body>
<header class="site-header">
  <nav class="main-nav">
    <a style="left:238px">ABOUT</a>
    <a style="left:315px">PRODUCTS</a>
    <a style="left:414px">WHERE TO BUY</a>
    <a style="left:537px">RECIPES</a>
    <a style="left:622px">REVIEWS</a>
  </nav>
  <div class="nav-cta">CONTACT
    <svg width="7" height="8" viewBox="0 0 7 8"><path d="M2 1l3 3-3 3" fill="none" stroke="#fff" stroke-width="1.4"/></svg>
  </div>
</header>
<div class="brand-tab"><span class="brand-name">Los Brava</span></div>

<section class="hero" role="img" aria-label="Abstract flame-shaped shapes in warm orange, red and dark green tones">
</section>
<h1 class="hero-title">CONTACT US</h1>
<svg class="abs" style="left:364px;top:192px" width="194" height="12" viewBox="0 0 194 12">
  <path d="M2 9 Q90 2 192 5 Q100 4 4 11 Z" fill="#fff"/>
</svg>

<div class="eyebrow">GET IN TOUCH</div>
<h2 class="section-title">CONTACT US</h2>
<svg class="abs" style="left:350px;top:395px" width="137" height="9" viewBox="0 0 137 9">
  <path d="M2 6 Q60 1 135 3 Q60 3 4 8 Z" fill="#c9202a"/>
</svg>
<p class="email-line">Email address :&nbsp; admin@losbravadip.example</p>

<form class="contact-form">
  <div class="field" style="left:40px;top:40px;width:256px;height:38px">First Name</div>
  <div class="field" style="left:305px;top:40px;width:256px;height:38px">Last Name</div>
  <div class="field" style="left:41px;top:87px;width:256px;height:38px">Email address</div>
  <div class="field" style="left:306px;top:87px;width:256px;height:38px">Phone</div>
  <div class="field message" style="left:42px;top:136px;width:520px;height:104px">Leave Message</div>
  <div class="send-btn">SEND MESSAGE</div>
</form>

<section class="follow-band" role="img" aria-label="Abstract flame shapes in red and orange">
  <div class="follow-title">FOLLOW US ON</div>
  <div class="social-ring" style="left:358px" aria-label="Social profile one"><span class="social-dot"></span></div>
  <div class="social-ring" style="left:434px" aria-label="Social profile two"><span class="social-dot"></span></div>
</section>

<footer class="site-footer">
  <div class="footer-divider-v"></div>
  <div class="footer-divider-h"></div>
  <div class="footer-brand">Los Brava</div>
  <div class="footer-nav">
    <span style="left:262px">ABOUT</span><i style="left:315px"></i>
    <span style="left:339px">PRODUCTS</span><i style="left:416px"></i>
    <span style="left:438px">WHERE TO BUY</span><i style="left:540px"></i>
    <span style="left:561px">RECIPES</span><i style="left:624px"></i>
    <span style="left:645px">REVIEWS</span><i style="left:711px"></i>
    <span style="left:733px">CONTACT</span>
  </div>
  <p class="legal" style="left:259px">© 2025 Larkfield Food Company. All rights reserved.</p>
  <span class="mini-social" style="left:584px"></span>
  <span class="mini-social" style="left:609px"></span>
  <p class="legal" style="left:649px">Privacy Policy</p>
  <p class="legal" style="left:720px">Terms of Use</p>
</footer>
</body>
</html>
```